Halberd Guard Services

Our Company is a security business which needs a cut edge design, the final product should have all relevant information and maintain a bold but modern and professional look.

Target Market(s)

A cut edge design which will attract any audience

Industry/Entity Type

Security

Contact Information for Business Card

HALBERD GUARD SERVICES

Gregor Lindqvist
Operations Manager
Phone: 0491 735 219

Email: info@halberdguard.com.au
Web: www.halberdguard.com.au

Requirements
Must have
• Must be double sided and contain all relevant information and the company logo.

```html
<!DOCTYPE html>
<html lang="en">
<head>
<meta charset="utf-8">
<title>Halberd Guard Services — Business Card</title>
<link href="https://fonts.googleapis.com/css2?family=Exo+2:wght@700&family=Open+Sans:wght@400;600&display=swap" rel="stylesheet">
<style>
  :root {
    --backdrop: #e4e4e2;
    --card-dark: #1f1c1b;
    --card-light: #ffffff;
    --steel: #5d7a84;
    --steel-deep: #3f5962;
    --silver-hi: #f2f2f2;
    --silver-lo: #a9abad;
    --accent: #f39200;
    --ink: #1a1a1a;
    --rule: #3f5962;
  }
  * { margin: 0; padding: 0; box-sizing: border-box; }
  html, body { width: 1200px; height: 951px; overflow: hidden; }
  body {
    background: var(--backdrop);
    font-family: "Open Sans", sans-serif;
    position: relative;
  }
  .card {
    position: absolute;
    width: 580px;
    height: 332px;
    border-radius: 22px;
    overflow: hidden;
    box-shadow: 0 6px 18px rgba(0,0,0,0.18);
  }

  /* Front side */
  .card-front {
    left: 70px;
    top: 110px;
    background: var(--card-dark);
  }
  .card-front .edges {
    position: absolute;
    inset: 0;
    width: 100%;
    height: 100%;
  }
  .front-brand {
    position: absolute;
    inset: 0;
    display: flex;
    flex-direction: column;
    align-items: center;
    justify-content: center;
    gap: 26px;
  }
  .brand-dot {
    width: 92px;
    height: 92px;
    border-radius: 50%;
    background: var(--steel);
  }
  .front-brand .brand-name {
    font-family: "Exo 2", sans-serif;
    font-weight: 700;
    font-size: 32px;
    letter-spacing: 1px;
    color: var(--steel);
    line-height: 1;
    white-space: nowrap;
  }

  /* Back side */
  .card-back {
    left: 550px;
    top: 500px;
    background: var(--card-light);
  }
  .back-brand {
    position: absolute;
    left: 38px;
    top: 36px;
    display: flex;
    align-items: center;
    gap: 12px;
  }
  .back-brand .brand-dot {
    width: 40px;
    height: 40px;
  }
  .back-brand .brand-name {
    font-family: "Exo 2", sans-serif;
    font-weight: 700;
    font-size: 21px;
    color: var(--steel-deep);
    line-height: 1;
    white-space: nowrap;
  }
  .divider {
    position: absolute;
    left: 20px;
    right: 40px;
    top: 152px;
    height: 1.5px;
    background: var(--rule);
  }
  .holder {
    position: absolute;
    right: 40px;
    top: 116px;
    text-align: right;
  }
  .holder-name {
    font-size: 21px;
    color: var(--accent);
    line-height: 1.3;
  }
  .holder-role {
    position: absolute;
    right: 40px;
    top: 156px;
    font-size: 16px;
    color: var(--ink);
    white-space: nowrap;
  }
  .contact-list {
    position: absolute;
    left: 22px;
    top: 202px;
    list-style: none;
  }
  .contact-list li {
    display: flex;
    align-items: center;
    gap: 8px;
    font-size: 17px;
    line-height: 23px;
    color: var(--ink);
  }
  .contact-list svg { width: 16px; height: 16px; flex: none; }
  .address {
    position: absolute;
    right: 40px;
    top: 238px;
    text-align: right;
    font-style: normal;
    font-size: 17px;
    line-height: 23px;
    color: var(--ink);
  }
</style>
</head>
<body>

  <section class="card card-front" aria-label="Business card, front">
    <svg class="edges" viewBox="0 0 580 332" preserveAspectRatio="none" aria-hidden="true">
      <defs>
        <linearGradient id="silver" x1="0" y1="0" x2="0" y2="1">
          <stop offset="0" stop-color="var(--silver-lo)"/>
          <stop offset="0.5" stop-color="var(--silver-hi)"/>
          <stop offset="1" stop-color="var(--silver-lo)"/>
        </linearGradient>
      </defs>
      <path d="M0 0 H30 Q62 166 30 332 H0 Z" fill="url(#silver)"/>
      <path d="M30 0 Q62 166 30 332" fill="none" stroke="var(--accent)" stroke-width="3"/>
      <path d="M580 0 H550 Q518 166 550 332 H580 Z" fill="url(#silver)"/>
      <path d="M550 0 Q518 166 550 332" fill="none" stroke="var(--accent)" stroke-width="3"/>
    </svg>
    <div class="front-brand">
      <span class="brand-dot" aria-hidden="true"></span>
      <span class="brand-name">HALBERD GUARD SERVICES</span>
    </div>
  </section>

  <section class="card card-back" aria-label="Business card, back">
    <div class="back-brand">
      <span class="brand-dot" aria-hidden="true"></span>
      <span class="brand-name">HALBERD GUARD SERVICES</span>
    </div>

    <div class="holder">
      <p class="holder-name">Gregor Lindqvist</p>
    </div>
    <div class="divider"></div>
    <p class="holder-role">Operations Manager</p>

    <ul class="contact-list">
      <li>
        <svg viewBox="0 0 16 16" aria-hidden="true"><path d="M4 1.5 L6.5 4.5 L5 6 Q6.5 9.5 10 11 L11.5 9.5 L14.5 12 L12.5 14.5 Q5 13.5 1.5 3.5 Z" fill="var(--accent)"/></svg>
        <span>0491 735 219</span>
      </li>
      <li>
        <svg viewBox="0 0 16 16" aria-hidden="true"><rect x="2" y="4" width="12" height="9" rx="2" fill="var(--accent)"/><rect x="5" y="2" width="6" height="3" rx="1" fill="var(--accent)"/></svg>
        <span>0491 735 218</span>
      </li>
      <li>
        <svg viewBox="0 0 16 16" aria-hidden="true"><rect x="1.5" y="3.5" width="13" height="9" rx="1.5" fill="var(--accent)"/><path d="M2 4 L8 9 L14 4" fill="none" stroke="#fff" stroke-width="1.3"/></svg>
        <span>info@halberdguard.com.au</span>
      </li>
      <li>
        <svg viewBox="0 0 16 16" aria-hidden="true"><circle cx="8" cy="8" r="6.5" fill="var(--accent)"/></svg>
        <span>www.halberdguard.com.au</span>
      </li>
    </ul>

    <address class="address">
      48 Tallow Ridge Rd.<br>
      Suite 12 - 040<br>
      Marlow, VIC 3081
    </address>
  </section>

</body>
</html>
```